Information One Page for Email

I am looking for a informative attachment I can send with an introductive email for Meridale Slab Works. Something I can also Mail.

Meridale Slab Works is the leader in Rebar Post Tension Cable Placement and Post Tension Cable repair. Outside of cable placement and repair we do concrete repair, Parking Garage restoration and
Updates

Content

Post Tension Repair and Concrete Restoration
Post-tensioning is a revolutionary method in concrete construction that enhances the strength and durability of structures. However, like all construction ele-ments, post-tension cables can experience wear and damage over time. Ensuring timely and effective repair is crucial for maintaining the safety and integrity of your building.
Why Post-Tension Cable Repair is Essential
1. **Structural Integrity**: Damaged or deteriorated cables can compromise the structural integrity of your building, leading to safety hazards and potential structural failures.
2. **Extended Lifespan**: Regular maintenance and repair of post-tension cables extend the lifespan of your structure, ensuring it remains safe and function-al for years to come.
3. **Cost-Effective**: Addressing cable issues early on prevents more severe damage and costly repairs down the line.
Common Signs of Post-Tension Cable Issues
- Cracks in concrete surfaces
- Unusual noises or popping sounds
- Visible cable ends or broken strands
- Water leakage through cracks
Our Repair Process
1. **Inspection and Assessment**: Our team conducts a thorough inspection to identify the extent of the damage and determine the appropriate repair meth-ods.
2. **Cable Repair or Replacement**: Depending on the severity, we either re-pair the existing cables or replace them with new ones to restore full functional-ity.
3. **Sealing and Protection**: After repairing, we seal the affected areas to protect against moisture and future damage.
4. **Quality Assurance**: We perform rigorous quality checks to ensure the repairs meet industry standards and the structure is safe for use.
Why Choose Us
- **Expertise and Experience**: With years of experience in post-tension cable repair, our team is skilled in handling even the most complex repairs efficiently and effectively.
- **Advanced Technology**: We use the latest technology and materials to ensure durable and long-lasting repairs.
- **Customer Satisfaction**: Our commitment to quality and customer satisfaction sets us apart. We work closely with our clients to ensure their needs are met and expectations exceeded.
Contact Us
If you suspect issues with your post-tension cables or need a routine inspection, don't hesitate to contact us. Our experts are ready to provide the best solutions to keep your structures safe and secure.
Ensure the safety and longevity of your building with our professional post-tension cable repair services. Trust us to deliver quality and reliability every time.

```html
<!DOCTYPE html>
<html lang="en">
<head>
<meta charset="utf-8">
<title>Meridale Slab Works – Post Tension Repair</title>
<link href="https://fonts.googleapis.com/css2?family=Noto+Serif:wght@500;600;700&family=Roboto:wght@400;500;700&display=swap" rel="stylesheet">
<style>
:root{
  --green:#0f6a38;
  --green-deep:#0a4a28;
  --ink:#1d1d1d;
  --band:#eceeed;
  --card:#575757;
  --rule:#c9cfcc;
  --white:#ffffff;
  --stage:#8a8a8a;
  --serif:"Noto Serif", Georgia, serif;
  --sans:"Roboto", Arial, sans-serif;
}
*{box-sizing:border-box;margin:0;padding:0}
html,body{width:886px;height:1200px;overflow:hidden;background:var(--stage)}
.flyer{position:absolute;left:144px;top:159px;width:598px;height:882px;background:var(--white);overflow:hidden;font-family:var(--sans);color:var(--ink)}
.abs{position:absolute}

.brand{left:34px;top:30px;display:flex;align-items:center;gap:8px;font-family:var(--serif);font-weight:600;font-size:17px;color:var(--green)}
.brand-mark{width:12px;height:12px;background:var(--green)}

.hero-photo{right:0;top:0;width:304px;height:255px;background:linear-gradient(135deg,#c9c6bf 0%,#9d9a93 45%,#6d6a64 100%);clip-path:polygon(28% 0,100% 0,100% 100%,0 100%,12% 60%)}

.headline{left:34px;top:100px;font-family:var(--serif);font-weight:600;font-size:22.5px;line-height:1.15;color:var(--ink)}
.headline span{color:var(--green);display:block}
.intro{left:34px;top:158px;width:260px;font-size:9.4px;line-height:1.25}

.band{left:0;top:255px;width:598px;height:310px;background:var(--band)}

.essential{left:33px;top:277px;width:268px;height:270px;background:var(--card);border-radius:12px;overflow:hidden;color:var(--white)}
.essential-head{background:var(--green);height:77px;padding:18px 22px;font-family:var(--serif);font-weight:600;font-size:16.5px;line-height:1.32}
.essential-list{list-style:none;padding:20px 20px 0 22px}
.essential-list li{display:flex;gap:10px;margin-bottom:14px}
.essential-list h4{font-family:var(--serif);font-weight:600;font-size:11.5px;margin-bottom:3px}
.essential-list p{font-size:8px;line-height:1.3}
.icon-w{flex:none;width:36px;height:36px;border-radius:50%;background:var(--white);display:flex;align-items:center;justify-content:center}

.choose-title,.signs-title,.process-title{font-family:var(--serif);font-weight:600;color:var(--green)}
.choose-title{left:334px;top:273px;font-size:16.5px}
.choose-list{left:334px;top:303px;width:230px;list-style:none}
.choose-list li{display:flex;gap:16px;margin-bottom:8px}
.icon-g{flex:none;width:36px;height:36px;border-radius:50%;background:var(--green);display:flex;align-items:center;justify-content:center;margin-top:4px}
.choose-list h4{font-family:var(--serif);font-weight:600;font-size:9.6px;margin-bottom:3px}
.choose-list p{font-size:7.6px;line-height:1.3}

.signs-title{left:334px;top:456px;font-size:16.5px;line-height:1.2}
.signs{left:334px;top:502px;width:240px;list-style:none;display:grid;grid-template-columns:110px 120px;row-gap:7px;font-size:8.6px;line-height:1.3;font-weight:500}
.signs li{display:flex;gap:6px}
.signs svg{flex:none;margin-top:1px}

.process-title{left:0;width:598px;top:576px;text-align:center;font-size:16.5px}
.steps{left:18px;top:607px;width:562px;display:grid;grid-template-columns:repeat(4,1fr);list-style:none}
.steps li{text-align:center;padding:0 8px;border-left:1px solid var(--rule);height:100px}
.steps li:first-child{border-left:none}
.step-num{display:inline-flex;width:25px;height:25px;border-radius:50%;background:var(--green);color:var(--white);align-items:center;justify-content:center;font-family:var(--serif);font-weight:600;font-size:14px}
.steps h4{font-family:var(--serif);font-weight:600;color:var(--green);font-size:11.3px;line-height:1.25;margin:4px 0 3px}
.steps p{font-size:7.6px;line-height:1.3}

.contact{left:0;top:731px;width:598px;height:151px;background:linear-gradient(180deg,var(--green) 0%,var(--green-deep) 70%);color:var(--white);text-align:center;padding:31px 36px 0}
.contact p{font-size:7.7px;line-height:1.3}
.call{margin-top:14px;font-family:var(--serif);font-weight:600;font-size:26px;display:flex;justify-content:center;align-items:center;gap:12px}
</style>
</head>
<body>
<div class="flyer">
  <div class="abs brand"><span class="brand-mark"></span>Meridale Slab Works</div>
  <div class="abs hero-photo" role="img" aria-label="Photo of a concrete building's slab edges under post-tension repair"></div>

  <h1 class="abs headline"><span>Post Tension Repair</span>and Concrete Restoration</h1>
  <p class="abs intro">Post-tensioning is a revolutionary method in concrete construction that enhances the strength and durability of structures. However, like all construction ele-ments, post-tension cables can experience wear and damage over time. Ensuring timely and effective repair is crucial for maintaining the safety and integrity of your building.</p>

  <div class="abs band"></div>

  <section class="abs essential">
    <h2 class="essential-head">Why Post-Tension Cable Repair is Essential</h2>
    <ul class="essential-list">
      <li><span class="icon-w"><svg width="20" height="20" viewBox="0 0 20 20" fill="#0f6a38"><path d="M10 2 2 7h16z"/><rect x="4" y="8" width="2" height="7"/><rect x="9" y="8" width="2" height="7"/><rect x="14" y="8" width="2" height="7"/><rect x="2" y="16" width="16" height="2"/></svg></span>
        <div><h4>Structural Integrity</h4><p>Damaged or deteriorated cables can compromise the structural integrity of your building, leading to safety hazards and potential structural failures.</p></div></li>
      <li><span class="icon-w"><svg width="20" height="20" viewBox="0 0 20 20" fill="none" stroke="#0f6a38" stroke-width="2"><rect x="5" y="3" width="10" height="14" rx="1"/><path d="M8 7h4M8 10h4M8 13h2"/></svg></span>
        <div><h4>Extended Lifespan</h4><p>Regular maintenance and repair of post-tension cables extend the lifespan of your structure, ensuring it</p></div></li>
      <li><span class="icon-w"><svg width="20" height="20" viewBox="0 0 20 20" fill="#0f6a38"><rect x="2" y="12" width="3" height="6"/><rect x="6" y="9" width="3" height="9"/><rect x="10" y="6" width="3" height="12"/><circle cx="16" cy="14" r="3"/><path d="M11 1 7 5h8z"/></svg></span>
        <div><h4>Cost-Effective</h4><p>Addressing cable issues early on prevents more severe damage and costly repairs down the line.</p></div></li>
    </ul>
  </section>

  <h2 class="abs choose-title">Why Choose Us</h2>
  <ul class="abs choose-list">
    <li><span class="icon-g"><svg width="18" height="18" viewBox="0 0 20 20" fill="none" stroke="#fff" stroke-width="2"><circle cx="10" cy="8" r="5"/><path d="M7 12l-2 6 5-2 5 2-2-6"/></svg></span>
      <div><h4>Expertise and Experience</h4><p>With years of experience in post-tension cable repair, our team is skilled in handling even the most complex repairs efficiently and effectively.</p></div></li>
    <li><span class="icon-g"><svg width="18" height="18" viewBox="0 0 20 20" fill="none" stroke="#fff" stroke-width="2"><circle cx="10" cy="10" r="4"/><path d="M10 1v4M10 15v4M1 10h4M15 10h4M4 4l2 2M14 14l2 2M16 4l-2 2M4 16l2-2"/></svg></span>
      <div><h4>Advanced Technology</h4><p>We use the latest technology and materials to ensure durable and long-lasting repairs.</p></div></li>
    <li><span class="icon-g"><svg width="18" height="18" viewBox="0 0 20 20" fill="#fff"><circle cx="6" cy="7" r="2.5"/><circle cx="14" cy="7" r="2.5"/><circle cx="10" cy="10" r="2.5"/><path d="M3 17a4 4 0 0 1 6-4 4 4 0 0 1 2 0 4 4 0 0 1 6 4z"/></svg></span>
      <div><h4>Customer Satisfaction</h4><p>Our commitment to quality and customer satisfaction sets us apart. We work closely with our clients to ensure their needs are met and expectations exceeded.</p></div></li>
  </ul>

  <h2 class="abs signs-title">Common Signs of<br>Post-Tension Cable Issues</h2>
  <ul class="abs signs">
    <li><svg width="14" height="14" viewBox="0 0 14 14" fill="none" stroke="#0f6a38" stroke-width="1.6"><circle cx="7" cy="7" r="6"/><path d="M4 7l2 2 4-4"/></svg>Cracks in concrete surfaces</li>
    <li><svg width="14" height="14" viewBox="0 0 14 14" fill="none" stroke="#0f6a38" stroke-width="1.6"><circle cx="7" cy="7" r="6"/><path d="M4 7l2 2 4-4"/></svg>Visible cable ends or broken strands</li>
    <li><svg width="14" height="14" viewBox="0 0 14 14" fill="none" stroke="#0f6a38" stroke-width="1.6"><circle cx="7" cy="7" r="6"/><path d="M4 7l2 2 4-4"/></svg>Unusual noises or popping sounds</li>
    <li><svg width="14" height="14" viewBox="0 0 14 14" fill="none" stroke="#0f6a38" stroke-width="1.6"><circle cx="7" cy="7" r="6"/><path d="M4 7l2 2 4-4"/></svg>Water leakage through cracks</li>
  </ul>

  <h2 class="abs process-title">Our Repair Process</h2>
  <ol class="abs steps">
    <li><span class="step-num">1</span><h4>Inspection and Assessment</h4><p>Our team conducts a inspection to identify the extent of the damage and determine the appropriate repair meth-ods.</p></li>
    <li><span class="step-num">2</span><h4>Cable Repair or Replacement</h4><p>Depending on the severity, we either re-pair the existing cables or replace them with new ones to restore full functional-ity.</p></li>
    <li><span class="step-num">3</span><h4>Sealing and Protection</h4><p>After repairing, we seal the affected areas to protect against moisture and future damage.</p></li>
    <li><span class="step-num">4</span><h4>Quality Assurance</h4><p>We perform rigorous quality checks to ensure the repairs meet industry standards and the structure is safe for use.</p></li>
  </ol>

  <footer class="abs contact">
    <p>If you suspect issues with your post-tension cables or need a routine inspection, don't hesitate to contact us. Our experts are ready to provide the best solutions to keep your structures safe and secure.</p>
    <p>Ensure the safety and longevity of your building with our professional post-tension cable repair services. Trust us to deliver quality and reliability every time.</p>
    <div class="call">Call Now
      <svg width="26" height="26" viewBox="0 0 26 26"><circle cx="13" cy="13" r="13" fill="#fff"/><path d="M9 7c1 0 2 2 2 3s-1 1-1 2c1 2 2 3 4 4 1 0 1-1 2-1s3 1 3 2-1 2-3 2c-4 0-9-5-9-9 0-2 1-3 2-3z" fill="#0f6a38"/></svg>
      (555) 014-2280</div>
  </footer>
</div>
</body>
</html>
```